Executive Business Card for Healthcare Company [Need Today]

I need a business card design for a healthcare company. The only branding the company has thus far is a logo. The cards will be utilized by company executives. The design I envision will be vibrant and appealing but with a corporate feel. They shouldn't be too casual or playful. I would like to complete this project TODAY if possible.

Target Market(s)

Healthcare vendors, other executives in healthcare and pharmaceuticals

Industry/Entity Type

Pharmaceutical

Contact Information for Business Card

See attachment

Font styles to use
Serif
Sans Serif

Colors

Designer to choose colors to be used in the design.

```html
<!DOCTYPE html>
<html lang="en">
<head>
<meta charset="utf-8">
<title>Corvane Therapeutics — Business Card</title>
<link rel="stylesheet" href="https://fonts.googleapis.com/css2?family=Crimson+Text:wght@400;600&family=Open+Sans:wght@300;400&display=swap">
<style>
  :root {
    --backdrop: #8fa8ae;
    --ink: #232a2a;
    --paper: #ffffff;
    --serif: "Crimson Text", Georgia, serif;
    --sans: "Open Sans", Arial, sans-serif;
  }
  * { box-sizing: border-box; margin: 0; padding: 0; }
  html, body { width: 1200px; height: 800px; overflow: hidden; }
  body { background: var(--backdrop); position: relative; }

  .card {
    position: absolute;
    left: 326px;
    width: 538px;
    height: 307px;
    overflow: hidden;
  }

  /* Front */
  .card-front { top: 24px; background: var(--ink); }
  .front-frame {
    position: absolute;
    left: 37px; top: 40px;
    width: 463px; height: 226px;
    border: 3px solid var(--paper);
  }
  .brand {
    position: absolute;
    display: flex;
    align-items: center;
    gap: 14px;
    font-family: var(--sans);
    font-weight: 300;
  }
  .brand-mark {
    border-radius: 50%;
    flex: none;
  }
  .brand-name { line-height: 1.05; }
  .front-brand { left: 112px; top: 98px; color: var(--paper); }
  .front-brand .brand-mark { width: 96px; height: 96px; border: 3px solid var(--paper); }
  .front-brand .brand-name { font-size: 34px; }

  /* Back */
  .card-back { top: 426px; background: var(--paper); color: var(--ink); }
  .back-brand { left: 33px; top: 34px; color: var(--ink); }
  .back-brand .brand-mark { width: 69px; height: 69px; border: 3px solid var(--ink); }
  .back-brand .brand-name { font-size: 22px; }

  .person {
    position: absolute;
    right: 27px; top: 28px;
    text-align: right;
    font-family: var(--serif);
  }
  .person-name { font-size: 38px; font-weight: 400; line-height: 1.05; }
  .person-title { font-size: 18.5px; line-height: 1.2; }

  .address {
    position: absolute;
    left: 19px; top: 140px;
    display: flex;
    gap: 6px;
    font-family: var(--serif);
    font-size: 15px;
    line-height: 1.3;
  }
  .address svg { flex: none; margin-top: 1px; }

  .social {
    position: absolute;
    left: 60px; top: 214px;
    width: 100px;
    text-align: center;
    font-family: var(--serif);
    font-size: 16.5px;
  }
  .social-links { display: flex; justify-content: center; gap: 6px; margin-top: 6px; }
  .social-links span { width: 19px; height: 19px; background: var(--ink); border-radius: 3px; }

  .divider {
    position: absolute;
    left: 264px; top: 124px;
    width: 2px; height: 130px;
    background: var(--ink);
  }

  .contacts {
    position: absolute;
    left: 282px; top: 118px;
    list-style: none;
    font-family: var(--sans);
    font-size: 17px;
  }
  .contacts li { display: flex; align-items: center; gap: 12px; height: 27px; margin-bottom: 12px; }
  .contacts li.email { font-size: 15.5px; }
  .contact-icon {
    width: 27px; height: 27px; border-radius: 50%;
    background: var(--ink);
    display: flex; align-items: center; justify-content: center;
    flex: none;
  }

  .footer-bar {
    position: absolute;
    top: 293px; height: 6px;
    background: var(--ink);
  }
  .footer-bar.left { left: 0; width: 191px; }
  .footer-bar.right { left: 346px; width: 192px; }
  .website {
    position: absolute;
    left: 191px; width: 155px; top: 284px;
    text-align: center;
    font-family: var(--serif);
    font-size: 14.5px;
  }
</style>
</head>
<body>

  <section class="card card-front" aria-label="Card front">
    <div class="front-frame"></div>
    <div class="brand front-brand">
      <span class="brand-mark"></span>
      <span class="brand-name">corvane<br>therapeutics</span>
    </div>
  </section>

  <section class="card card-back" aria-label="Card back">
    <div class="brand back-brand">
      <span class="brand-mark"></span>
      <span class="brand-name">corvane<br>therapeutics</span>
    </div>

    <div class="person">
      <h1 class="person-name">Martin Hale</h1>
      <p class="person-title">Senior Director of Marketing</p>
    </div>

    <div class="address">
      <svg width="26" height="26" viewBox="0 0 26 26" aria-hidden="true">
        <circle cx="13" cy="13" r="13" fill="#232a2a"/>
        <path d="M13 6a4.5 4.5 0 0 0-4.5 4.5C8.5 14 13 20 13 20s4.5-6 4.5-9.5A4.5 4.5 0 0 0 13 6z" fill="#fff"/>
        <circle cx="13" cy="10.5" r="1.7" fill="#232a2a"/>
      </svg>
      <p>118 W Oak Avenue Ridgefield<br>GA 30190</p>
    </div>

    <div class="social">
      <p>Find Us on:</p>
      <div class="social-links"><span></span><span></span><span></span><span></span></div>
    </div>

    <div class="divider"></div>

    <ul class="contacts">
      <li>
        <span class="contact-icon">
          <svg width="15" height="15" viewBox="0 0 24 24" aria-hidden="true"><path fill="#fff" d="M6.6 10.8a15.1 15.1 0 0 0 6.6 6.6l2.2-2.2c.3-.3.7-.4 1-.2 1.1.4 2.3.6 3.6.6.6 0 1 .4 1 1V20c0 .6-.4 1-1 1A17 17 0 0 1 3 4c0-.6.4-1 1-1h3.5c.6 0 1 .4 1 1 0 1.3.2 2.5.6 3.6.1.3 0 .7-.2 1z"/></svg>
        </span>
        555-201-4478
      </li>
      <li>
        <span class="contact-icon">
          <svg width="16" height="16" viewBox="0 0 24 24" aria-hidden="true"><path fill="#fff" d="M3 9c0-2 4-4 9-4s9 2 9 4v1.5h-4V8.5c-1.3-.5-3-.8-5-.8s-3.7.3-5 .8v2H3z"/><path fill="#fff" d="M7 11h10l2 8H5z"/><circle cx="12" cy="15" r="2" fill="#232a2a"/></svg>
        </span>
        555-201-4490
      </li>
      <li class="email">
        <span class="contact-icon">
          <svg width="15" height="15" viewBox="0 0 24 24" aria-hidden="true"><rect x="2" y="5" width="20" height="14" rx="1" fill="#fff"/><path d="M2.5 5.5 12 13l9.5-7.5" fill="none" stroke="#232a2a" stroke-width="1.5"/></svg>
        </span>
        mhale@corvanerx.com
      </li>
    </ul>

    <div class="footer-bar left"></div>
    <p class="website">www.website.com</p>
    <div class="footer-bar right"></div>
  </section>

</body>
</html>
```